Redesign Two Website Pages (Homepage & Features) — Modern, Responsive, and Visually Engaging

We’re looking to redesign two pages of our website:

Homepage: https://velmorta.com
Features Page: https://velmorta.com/features

We already have a preliminary design in Figma for the homepage, but it currently feels too plain. Please don’t use this Figma file provided. It was only shared for facilitate using the current website content and not as a source for inspiration. Use your creativity to bring something fresh and less dull as the current design.

We want to enhance it with visually engaging elements, such as illustrations, graphics, or images that align with the content and the application’s purpose, making the design more dynamic and marketing-oriented.

Requirements:
- Create modern, visually appealing designs for both pages.
- Include relevant visuals (images or vector graphics) that complement the content and improve user engagement.
- Ensure full responsiveness across all major viewports: desktop, tablet, and mobile.
- Deliver the final design in Figma format.
- You can choose any colour palette that best fits the concept, but please retain the existing content from the live website.
- We’re looking for a clean, modern, and commercially appealing design that effectively communicates the value of our product.

Target Market(s)

B2B

Number of Pages Required

2 page

Font styles to use
Sans Serif

Requirements
Must have
• Images and graphics to make the design and product more attractive.

```html
<!DOCTYPE html>
<html lang="en">
<head>
<meta charset="utf-8">
<title>VELMORTA — Steady answers for every audit</title>
<link href="https://fonts.googleapis.com/css2?family=Poppins:ital,wght@0,300;0,400;0,500;0,600;0,700;1,300;1,400&display=swap" rel="stylesheet">
<style>
:root{
  --blue:#0a6ed1;
  --blue-dark:#075db3;
  --ink:#111418;
  --text:#2b2f36;
  --muted:#6c727c;
  --pale:#f2f7fc;
  --grey-box:#f5f5f6;
  --line:#e6e9ee;
  --white:#ffffff;
  --star:#f5c518;
}
*{box-sizing:border-box;margin:0;padding:0}
html,body{width:1200px;height:3322px;overflow:hidden}
body{font-family:"Poppins",sans-serif;color:var(--text);background:var(--white);position:relative}
a{color:inherit;text-decoration:none}
.btn{position:absolute;display:flex;align-items:center;justify-content:center;border-radius:40px;font-weight:700;font-size:15px;letter-spacing:.2px;text-transform:uppercase;white-space:nowrap}
.btn-solid{background:var(--blue);color:var(--white)}
.btn-outline{border:2px solid var(--blue);color:var(--blue);background:var(--white)}
.btn-white{background:var(--white);color:var(--blue)}
.btn-ghost{border:2px solid var(--white);color:var(--white)}

/* header */
.site-header{position:absolute;top:0;left:0;width:1200px;height:68px;background:var(--white)}
.brand{position:absolute;display:flex;align-items:center;gap:10px}
.brand-mark{width:30px;height:30px;border-radius:50%;background:var(--blue);flex:none}
.brand-name{font-size:19px;font-weight:500;line-height:1.05;color:var(--ink)}
.brand-tag{font-size:13px;font-weight:400;color:var(--text)}
.nav{position:absolute;top:26px;left:549px;display:flex;gap:37px;font-size:14px;font-weight:500;color:var(--ink)}
.nav .active{color:var(--blue);border-bottom:1px solid var(--blue);padding-bottom:2px}

/* hero */
.hero{position:absolute;top:68px;left:0;width:1200px;height:574px;overflow:hidden}
.hero-photo{position:absolute;inset:0;background:linear-gradient(90deg,#f3f3f2 0%,#eeeeec 40%,#c9ced3 62%,#6c7c8e 78%,#2f4a66 90%,#b9bcc0 100%)}
.hero h1{position:absolute;left:143px;top:84px;font-size:43px;line-height:60px;font-weight:500;color:var(--ink)}
.hero h1 b{font-weight:700}
.hero h1 .hl{color:var(--blue);font-weight:700}
.hero-rule{position:absolute;left:0;top:220px;width:396px;height:4px;background:var(--blue)}
.hero-dots{position:absolute;left:402px;top:219px;display:flex;gap:4px}
.hero-dots i{width:6px;height:6px;border-radius:50%;background:var(--blue);display:block}
.hero p{position:absolute;left:143px;top:244px;width:520px;font-size:16.5px;line-height:27px;color:var(--ink)}
.checks{position:absolute;display:flex;gap:22px;font-size:13px;color:var(--text)}
.checks span{display:flex;align-items:center;gap:6px}
.tick{width:12px;height:12px;border-radius:50%;background:var(--blue);display:inline-flex;align-items:center;justify-content:center;flex:none}

/* features */
.section-title{position:absolute;left:0;width:1200px;text-align:center;font-size:34px;font-weight:400;color:var(--ink)}
.section-title b{font-weight:700}
.section-sub{position:absolute;left:0;width:1200px;text-align:center;font-size:18px;color:var(--ink)}
.feature-photo{position:absolute;left:0;top:816px;width:585px;height:486px;background:linear-gradient(135deg,#5a6470 0%,#9aa3ad 45%,#d9dde2 70%,#8a929c 100%)}
.timeline{position:absolute;left:644px;top:890px;width:2px;height:200px;background:linear-gradient(#0a6ed1,rgba(10,110,209,0))}
.timeline-dot{position:absolute;left:636px;top:893px;width:18px;height:18px;border-radius:50%;background:var(--blue);box-shadow:0 0 0 4px #d6e7f8}
.feature-card{position:absolute;left:680px;width:374px;display:flex;gap:20px;padding:22px 18px}
.feature-card h3{font-size:18px;font-weight:500;margin-bottom:6px}
.feature-card p{font-size:13.5px;line-height:23px}
.feature-card.active{top:839px;height:125px;background:var(--blue);color:var(--white);border-radius:4px}
.feature-card.active::before{content:"";position:absolute;left:-10px;top:54px;border:10px solid transparent;border-right-color:var(--blue);border-left:0}
.feature-card.next{top:964px;color:#6d727a;border-bottom:1px solid var(--line)}
.feature-card.next p{color:#9aa0a8}
.feature-card.faded{top:1090px;color:#c3c7cc}
.feature-card.faded p{color:#d5d8dc}
.pager{position:absolute;left:1094px;top:994px;display:flex;flex-direction:column;gap:4px}
.pager i{display:block;width:8px;height:8px;border-radius:50%;border:1px solid #8c939b}
.pager i.on{background:var(--blue);border-color:var(--blue)}

/* stats */
.stats{position:absolute;left:0;top:1383px;width:717px;height:347px;background:var(--pale)}
.stats-photo{position:absolute;left:717px;top:1383px;width:483px;height:347px;background:linear-gradient(120deg,#e9ebee 0%,#cfd4da 40%,#9aa5b1 70%,#4b5563 100%)}
.stat{position:absolute;display:flex;gap:25px}
.stat svg{flex:none}
.stat-num{font-size:32px;font-weight:700;color:var(--blue);line-height:40px}
.stat-rule{width:48px;height:3px;background:var(--blue);margin:10px 0 14px}
.stat-label{font-size:14px;color:var(--ink)}

/* cta band */
.cta{position:absolute;left:0;top:1730px;width:1200px;height:327px;background:linear-gradient(135deg,#0b6fd3,#0862c0);color:var(--white);text-align:center}
.cta h2{position:absolute;top:56px;left:0;width:100%;font-size:34px;font-weight:400}
.cta h2 b{font-weight:700}
.cta .lead{position:absolute;top:116px;left:0;width:100%;font-size:17px;font-weight:500}
.cta .checks{top:162px;left:0;width:100%;justify-content:center;color:var(--white)}
.cta .tick{background:var(--white)}

/* comparison */
.compare{position:absolute;top:2240px;width:442px;height:214px;padding:30px 32px;border-radius:4px}
.compare h4{font-size:18px;font-weight:500;margin-bottom:16px}
.compare li{list-style:none;font-size:14px;color:var(--ink);display:flex;align-items:center;gap:8px;margin-bottom:12px;white-space:nowrap}
.compare.without{left:144px;background:var(--grey-box)}
.compare.without h4{color:var(--ink)}
.compare.with{left:613px;background:var(--pale)}
.compare.with h4{color:var(--blue)}
.xmark{width:12px;height:12px;border-radius:50%;background:var(--ink);display:inline-flex;align-items:center;justify-content:center;flex:none}

/* testimonials */
.quote{position:absolute;top:2637px;width:294px;height:266px;background:var(--white);box-shadow:0 2px 12px rgba(20,30,50,.08);padding:24px 22px}
.stars{color:var(--star);font-size:16px;letter-spacing:2px}
.quote blockquote{margin-top:14px;font-size:14px;line-height:23px;font-style:italic;font-weight:300;color:var(--muted)}
.author{position:absolute;left:22px;top:182px;display:flex;gap:14px;align-items:center}
.avatar{width:56px;height:56px;border-radius:50%;color:var(--white);font-size:22px;font-weight:600;display:flex;align-items:center;justify-content:center;flex:none}
.author .name{font-size:14px;color:var(--ink)}
.author .role{font-size:11px;color:var(--blue);line-height:19px}

/* footer */
.site-footer{position:absolute;left:0;top:2983px;width:1200px;height:339px;background:var(--blue);color:var(--white)}
.site-footer .brand-name,.site-footer .brand-tag{color:var(--white)}
.site-footer .brand-mark{background:var(--white)}
.footer-rule{position:absolute;left:143px;width:912px;height:1px;background:rgba(255,255,255,.28)}
.footer-col{position:absolute;top:148px;font-size:14px;line-height:24px}
.footer-col h5{font-size:16px;font-weight:500;margin-bottom:6px;text-transform:uppercase}
.contact h5{text-transform:none;display:flex;align-items:center;gap:8px;margin-bottom:0}
.contact p{padding-left:27px;margin-bottom:12px}
.copyright{position:absolute;top:305px;left:0;width:100%;text-align:center;font-size:14px}
</style>
</head>
<body>

<header class="site-header">
  <a class="brand" href="https://velmorta.com" style="left:143px;top:16px">
    <span class="brand-mark"></span>
    <span><span class="brand-name">VELMORTA</span><br><span class="brand-tag">Steady answers for every audit</span></span>
  </a>
  <nav class="nav">
    <a class="active" href="https://velmorta.com/features">FEATURES</a>
    <a href="#">PRICING</a>
    <a href="#">DEMO</a>
  </nav>
  <a class="btn btn-solid" href="#" style="left:823px;top:16px;width:111px;height:40px;font-size:14px">Sign Up</a>
  <a class="btn btn-outline" href="#" style="left:943px;top:16px;width:112px;height:40px;font-size:14px">Sign In</a>
</header>

<section class="hero">
  <div class="hero-photo" role="img" aria-label="Photo of an auditor in glasses reviewing documents at a laptop in a bright office"></div>
  <h1>Cut Audit <b>Time by</b> <span class="hl">60%</span><br><b>Without Cutting</b> Corners</h1>
  <div class="hero-rule"></div>
  <div class="hero-dots"><i></i><i></i></div>
  <p>The only audit platform that combines AI-powered template generation, real-time collaboration, and intelligent compliance tracking. Join leading firms completing audits 3x faster with 99.9% accuracy.</p>
  <div class="checks" style="left:143px;top:370px">
    <span><i class="tick"><svg width="8" height="8" viewBox="0 0 8 8"><path d="M1.5 4l1.7 1.7L6.5 2.3" stroke="#fff" stroke-width="1.3" fill="none"/></svg></i>No Credit Card Required</span>
    <span><i class="tick"><svg width="8" height="8" viewBox="0 0 8 8"><path d="M1.5 4l1.7 1.7L6.5 2.3" stroke="#fff" stroke-width="1.3" fill="none"/></svg></i>14-day Free Trial</span>
    <span><i class="tick"><svg width="8" height="8" viewBox="0 0 8 8"><path d="M1.5 4l1.7 1.7L6.5 2.3" stroke="#fff" stroke-width="1.3" fill="none"/></svg></i>Cancel Anytime</span>
  </div>
  <a class="btn btn-solid" href="#" style="left:143px;top:416px;width:200px;height:51px">Start Free Trial</a>
  <a class="btn btn-outline" href="#" style="left:352px;top:416px;width:199px;height:51px">Schedule Demo</a>
</section>

<h2 class="section-title" style="top:698px">Everything <b>You Need to Scale Your</b> Audit <b>Practice</b></h2>
<p class="section-sub" style="top:760px">From solo practitioners to Big 4 firms, we’ve built the features that matter</p>

<div class="feature-photo" role="img" aria-label="Photo of a businessman working at a laptop beside a humanoid robot"></div>
<div class="timeline"></div>
<div class="timeline-dot"></div>

<div class="feature-card active">
  <svg width="50" height="50" viewBox="0 0 50 50" fill="none" stroke="#fff" stroke-width="1.6"><path d="M25 8c-9 0-15 6-15 14 0 5 3 8 4 11v7h14v-5h5c2 0 3-1 3-3v-5l4-1-4-7c0-7-5-11-11-11z"/><circle cx="24" cy="22" r="4"/><path d="M24 14v4M24 26v4M16 22h4M28 22h4"/></svg>
  <div><h3>AI-Powered Templates</h3><p>Generate industry-specific audit templates in 30 seconds.</p></div>
</div>
<div class="feature-card next">
  <svg width="60" height="60" viewBox="0 0 60 60" fill="none" stroke="#8a9099" stroke-width="1.5"><path d="M8 30l10-12 10 4 8-4 16 12-14 14-12-8-10 6z"/><path d="M22 34l6 6M28 30l6 6M34 28l6 6"/><path d="M14 16a20 20 0 0 1 32 0"/></svg>
  <div><h3>Real-Time Collaboration</h3><p>Your entire team works together seamlessly.</p></div>
</div>
<div class="feature-card faded">
  <svg width="60" height="60" viewBox="0 0 60 60" fill="none" stroke="#c8ccd1" stroke-width="1.5"><rect x="8" y="8" width="30" height="40" rx="2"/><path d="M14 30h18M14 36h12"/><circle cx="23" cy="19" r="5"/><circle cx="42" cy="42" r="9"/><path d="M48 48l7 7"/></svg>
  <div><h3>Evidence Management</h3><p>Attach documents, screenshots, and recordings directly to audit items.</p></div>
</div>
<a class="btn btn-solid" href="#" style="left:680px;top:1231px;width:151px;height:48px;font-size:14px">Learn More</a>
<div class="pager"><i></i><i class="on"></i><i></i><i></i></div>

<section class="stats">
  <div class="stat" style="left:143px;top:70px">
    <svg width="75" height="75" viewBox="0 0 75 75" fill="none" stroke="#0a6ed1" stroke-width="2"><rect x="4" y="6" width="44" height="60" rx="2"/><path d="M14 56V44M24 56V38M34 56V46"/><circle cx="52" cy="28" r="13"/><path d="M46 28l4 4 8-8M61 37l10 10"/></svg>
    <div><div class="stat-num">300+</div><div class="stat-rule"></div><div class="stat-label">Audit Firms</div></div>
  </div>
  <div class="stat" style="left:447px;top:70px">
    <svg width="75" height="75" viewBox="0 0 75 75" fill="none" stroke="#0a6ed1" stroke-width="2"><path d="M37 6l18 7v14c0 12-8 20-18 24-10-4-18-12-18-24V13z"/><path d="M29 29l6 6 11-12"/><path d="M6 40l8 16 14 10M69 40l-8 16-14 10"/></svg>
    <div><div class="stat-num">1000+</div><div class="stat-rule"></div><div class="stat-label">Audits Completed</div></div>
  </div>
  <div class="stat" style="left:143px;top:198px">
    <svg width="75" height="75" viewBox="0 0 75 75" fill="none" stroke="#0a6ed1" stroke-width="2"><rect x="4" y="8" width="44" height="60" rx="2"/><path d="M12 44h28M12 52h22M12 60h16"/><circle cx="26" cy="24" r="9"/><path d="M22 24l3 3 6-6M44 64l20-20 6 6-20 20z"/></svg>
    <div><div class="stat-num">99.9%</div><div class="stat-rule"></div><div class="stat-label">Compliance Rate</div></div>
  </div>
  <div class="stat" style="left:447px;top:198px">
    <svg width="75" height="75" viewBox="0 0 75 75" fill="none" stroke="#0a6ed1" stroke-width="2"><path d="M37 4l3 6 7 1-5 5 1 7-6-3-6 3 1-7-5-5 7-1zM14 14l2 4 5 1-4 3 1 5-4-2-4 2 1-5-4-3 5-1zM60 14l2 4 5 1-4 3 1 5-4-2-4 2 1-5-4-3 5-1z"/><circle cx="34" cy="40" r="9"/><path d="M16 70c0-11 8-18 18-18 5 0 9 2 12 5"/><circle cx="56" cy="60" r="11"/><path d="M51 60l4 4 7-7"/></svg>
    <div><div class="stat-num">4.9/5</div><div class="stat-rule"></div><div class="stat-label">Customer Rating</div></div>
  </div>
</section>
<div class="stats-photo" role="img" aria-label="Photo of business people shaking hands across a meeting table"></div>

<section class="cta">
  <h2><b>Ready to</b> Transform <b>Your Audit</b> Practice?</h2>
  <p class="lead">Join 300+ firms saving millions on audit costs. Start your free trial today and see results in your first audit.</p>
  <div class="checks">
    <span><i class="tick"><svg width="8" height="8" viewBox="0 0 8 8"><path d="M1.5 4l1.7 1.7L6.5 2.3" stroke="#0a6ed1" stroke-width="1.3" fill="none"/></svg></i>No Credit Card Required</span>
    <span><i class="tick"><svg width="8" height="8" viewBox="0 0 8 8"><path d="M1.5 4l1.7 1.7L6.5 2.3" stroke="#0a6ed1" stroke-width="1.3" fill="none"/></svg></i>14-day Free Trial</span>
    <span><i class="tick"><svg width="8" height="8" viewBox="0 0 8 8"><path d="M1.5 4l1.7 1.7L6.5 2.3" stroke="#0a6ed1" stroke-width="1.3" fill="none"/></svg></i>Cancel Anytime</span>
  </div>
  <a class="btn btn-white" href="#" style="left:396px;top:215px;width:232px;height:43px;font-size:14px">Start 14-day Free Trial</a>
  <a class="btn btn-ghost" href="#" style="left:637px;top:215px;width:166px;height:43px;font-size:14px">Schedule Demo</a>
</section>

<h2 class="section-title" style="top:2125px"><b>Stop Losing</b> $50K+ <b>Per Year on</b> Manual Audits</h2>
<p class="section-sub" style="top:2186px">Your team spends 70% of audit time on repetitive tasks. We fix that.</p>

<div class="compare without">
  <h4>Without VELMORTA:</h4>
  <ul>
    <li><i class="xmark"><svg width="6" height="6" viewBox="0 0 6 6"><path d="M1 1l4 4M5 1L1 5" stroke="#fff" stroke-width="1.2"/></svg></i>200+ hours creating templates from scratch</li>
    <li><i class="xmark"><svg width="6" height="6" viewBox="0 0 6 6"><path d="M1 1l4 4M5 1L1 5" stroke="#fff" stroke-width="1.2"/></svg></i>Version control chaos with shared spreadsheets</li>
    <li><i class="xmark"><svg width="6" height="6" viewBox="0 0 6 6"><path d="M1 1l4 4M5 1L1 5" stroke="#fff" stroke-width="1.2"/></svg></i>60% error rate from manual data entry</li>
    <li><i class="xmark"><svg width="6" height="6" viewBox="0 0 6 6"><path d="M1 1l4 4M5 1L1 5" stroke="#fff" stroke-width="1.2"/></svg></i>Compliance violations risk $100K+ fines</li>
  </ul>
</div>
<div class="compare with">
  <h4>With VELMORTA:</h4>
  <ul>
    <li><i class="tick"><svg width="8" height="8" viewBox="0 0 8 8"><path d="M1.5 4l1.7 1.7L6.5 2.3" stroke="#fff" stroke-width="1.3" fill="none"/></svg></i>AI generates templates in 30 seconds</li>
    <li><i class="tick"><svg width="8" height="8" viewBox="0 0 8 8"><path d="M1.5 4l1.7 1.7L6.5 2.3" stroke="#fff" stroke-width="1.3" fill="none"/></svg></i>Real-time collaboration with audit trail</li>
    <li><i class="tick"><svg width="8" height="8" viewBox="0 0 8 8"><path d="M1.5 4l1.7 1.7L6.5 2.3" stroke="#fff" stroke-width="1.3" fill="none"/></svg></i>Automated validation catches 99% of errors</li>
    <li><i class="tick"><svg width="8" height="8" viewBox="0 0 8 8"><path d="M1.5 4l1.7 1.7L6.5 2.3" stroke="#fff" stroke-width="1.3" fill="none"/></svg></i>Built-in compliance for ISO, GDPR, PCI DSS</li>
  </ul>
</div>

<h2 class="section-title" style="top:2527px"><b>Audit</b> Leaders <b>Choose VELMORTA</b></h2>
<p class="section-sub" style="top:2589px">See why we’re rated 4.9/5 by 500+ audit professionals</p>

<article class="quote" style="left:145px">
  <div class="stars">★★★★★</div>
  <blockquote>"We've reduced audit completion time from 3 weeks to 1 week. The AI templates alone saved us $200K in the first year. This is a game-changer for mid-size firms."</blockquote>
  <div class="author"><span class="avatar" style="background:#3d4b57">DW</span><div><div class="name">Dana Whitfield</div><div class="role">Partner, Whitfield &amp; Lowe CPA</div></div></div>
</article>
<article class="quote" style="left:453px">
  <div class="stars">★★★★★</div>
  <blockquote>"Our compliance rate went from 85% to 99.9%. The platform catches issues we'd never spot manually. We've avoided multiple six-figure penalties."</blockquote>
  <div class="author"><span class="avatar" style="background:#3f9a4c">MI</span><div><div class="name">Marco Ilardi</div><div class="role">Compliance Director, Ledgerline</div></div></div>
</article>
<article class="quote" style="left:760px">
  <div class="stars">★★★★★</div>
  <blockquote>"Best investment we've made. Our team can handle 3x more clients without adding headcount. ROI was positive in month one."</blockquote>
  <div class="author"><span class="avatar" style="background:#7a2238">JP</span><div><div class="name">Joanna Pruett</div><div class="role">Managing Director, Pruett<br>Audit Group</div></div></div>
</article>

<footer class="site-footer">
  <a class="brand" href="https://velmorta.com" style="left:143px;top:52px">
    <span class="brand-mark"></span>
    <span><span class="brand-name">VELMORTA</span><br><span class="brand-tag">Steady answers for every audit</span></span>
  </a>
  <a class="btn btn-white" href="#" style="left:647px;top:46px;width:232px;height:43px;font-size:14px">Start 14-day Free Trial</a>
  <a class="btn btn-ghost" href="#" style="left:888px;top:46px;width:166px;height:43px;font-size:14px">Schedule Demo</a>
  <div class="footer-rule" style="top:121px"></div>

  <div class="footer-col contact" style="left:143px">
    <h5><svg width="18" height="18" viewBox="0 0 18 18"><path d="M4 2l3 3-2 2c1 2 3 4 5 5l2-2 3 3-2 3C7 16 2 11 1 4z" fill="#fff"/></svg>Phone</h5>
    <p>+1-555-014-2290</p>
    <h5><svg width="18" height="18" viewBox="0 0 18 18"><rect x="1" y="3" width="16" height="12" rx="1" fill="#fff"/><path d="M2 4l7 6 7-6" stroke="#0a6ed1" stroke-width="1.4" fill="none"/></svg>Email</h5>
    <p>hello@velmorta.com</p>
  </div>
  <div class="footer-col" style="left:418px"><h5>Product</h5><a href="https://velmorta.com/features">Features</a><br>Pricing<br>Demo<br>Sign In</div>
  <div class="footer-col" style="left:651px"><h5>Company</h5>About<br>Contact<br>System Status</div>
  <div class="footer-col" style="left:945px"><h5>Legal</h5>Privacy Policy<br>Terms of Service<br>Security<br>Compliance</div>

  <div class="footer-rule" style="top:288px"></div>
  <p class="copyright">© 2025 VELMORTA &nbsp;-&nbsp; All Rights Reserved</p>
</footer>

</body>
</html>
```